Advanced Therapeutic Massage Therapist

I need a business card advertising my massage services as an advanced therapeutic massage therapist. I offer advanced therapeutic massage, swedish and deep tissue. I want to create a simple, professional and feminine card. I like bright colours and creativity.

I prefer a bold and experimental approach rather than something status-quo. A card to suggest therapeutic healing through dynamic massage. Motifs, shapes or layout which suggest movement and flow.
Updates

Target Market(s)

Everybody!

Industry/Entity Type

Health And Wellness

Contact Information for Business Card

The card should include:
My name, logo, services offered and my contact details.

Sláine Dunleavy
Massage Therapist

- Swedish - Deep Tissue - Advanced Therapeutic

Phone: (+353) 87 216 4093
Email: regenerate@slainedunleavy-example.com
Website: www.slainedunlevy-example.com

Font styles to use
Serif
Sans Serif
Decorative
Script

Colors

Designer to choose colors to be used in the design.

Requirements
Must have
• An example may contain something like this, yet concise:
• "Sláine Dunleavy
• Massage Therapist
• - Swedish - Deep Tissue - Advanced Therapeutic"
Nice to have
• This sentence is optional:
• Imagery such as a logo or symbol. I have attached a file containing a logo I had produced however the name is incorrect now as it is "Sláine" not "Nelly". It could be edited to change it to Sláine.
• I have sent the file as .psd .jpg. .pdf and .png
• I like when the card conveys energy, movement, pressure points, flow etc.
• I just like the designer to follow their own style and ideas. I like bright colours but must have a lot of a base colour to offset it. I really prefer them to follow their own inspiration. That is my preference.
Should not have
• Pine trees, non-native trees to Britain and Ireland, exotic flowers or animals that are not native to Britain and Ireland.
• I don't like brown as the background colour of the card.
• The cars shouldn't look like a wedding invitation i.e too many floral type designs.

```html
<!DOCTYPE html>
<html lang="en">
<head>
<meta charset="utf-8">
<title>Sláine Dunleavy – Massage Therapist</title>
<link rel="stylesheet" href="https://fonts.googleapis.com/css2?family=Kaushan+Script&family=Open+Sans:wght@400&display=swap">
<style>
  :root {
    --page: #e7e4e0;
    --card: #f4f2ef;
    --mint: #9dd3bd;
    --gold: #c9a045;
    --gold-soft: #e6cf94;
    --ink: #1c1c1c;
  }
  html, body {
    margin: 0;
    width: 1200px;
    height: 900px;
    overflow: hidden;
    background: var(--page);
  }
  .card {
    position: absolute;
    left: 120px;
    top: 152px;
    width: 960px;
    height: 596px;
    background: var(--card);
    box-shadow: 0 10px 30px rgba(0,0,0,.12);
    overflow: hidden;
    font-family: "Open Sans", Arial, sans-serif;
    color: var(--ink);
  }
  .card__shapes {
    position: absolute;
    inset: 0;
  }
  .card__details {
    position: absolute;
    left: 53px;
    top: 52px;
    width: 420px;
  }
  .card__name {
    margin: 0;
    font-family: "Kaushan Script", cursive;
    font-weight: 400;
    font-size: 44px;
    line-height: 1;
    white-space: nowrap;
  }
  .card__role {
    margin: 4px 0 0;
    font-size: 23px;
  }
  .contact {
    list-style: none;
    margin: 40px 0 0;
    padding: 0;
    font-size: 23px;
    line-height: 35px;
  }
  .contact li {
    display: flex;
    align-items: center;
    gap: 10px;
    white-space: nowrap;
  }
  .contact svg { width: 20px; height: 20px; flex: none; }
  .services {
    list-style: none;
    margin: 22px 0 0;
    padding: 0;
    font-size: 23px;
    line-height: 34px;
  }
  .services li::before {
    content: "";
    display: inline-block;
    width: 14px;
    height: 14px;
    margin-right: 12px;
    border-radius: 50%;
    background: var(--ink);
    vertical-align: 1px;
  }
  .card__summary {
    margin: 20px 0 0;
    font-size: 23px;
    line-height: 34px;
    white-space: nowrap;
  }
</style>
</head>
<body>
  <div class="card">
    <svg class="card__shapes" width="960" height="596" viewBox="0 0 960 596">
      <defs>
        <linearGradient id="vine-tone" x1="0" y1="0" x2="1" y2="0">
          <stop offset="0" stop-color="var(--gold-soft)" stop-opacity=".75"/>
          <stop offset="1" stop-color="var(--gold-soft)" stop-opacity="0"/>
        </linearGradient>
        <radialGradient id="emblem-tone" cx=".5" cy=".5" r=".5">
          <stop offset="0" stop-color="#a9dccb"/>
          <stop offset=".85" stop-color="#8fcbb5"/>
          <stop offset="1" stop-color="var(--gold)"/>
        </radialGradient>
      </defs>
      <path class="vine-band" role="img" aria-label="Gold leafy vine ornament following the curve"
            d="M295 0 H380 C575 60 575 536 380 596 H295 C505 536 505 60 295 0 Z"
            fill="url(#vine-tone)"/>
      <path class="mint-panel" d="M0 0 H295 C505 60 505 536 295 596 H0 Z" fill="var(--mint)"/>
      <path class="gold-edge" d="M295 0 C505 60 505 536 295 596" fill="none" stroke="var(--gold)" stroke-width="4"/>
      <circle class="emblem-ring" role="img" aria-label="Gold vine wreath around the emblem"
              cx="725" cy="297" r="165" fill="none" stroke="var(--gold-soft)" stroke-width="14" opacity=".7"/>
      <circle class="emblem" role="img" aria-label="Gold ornamental tree emblem on mint circle"
              cx="725" cy="297" r="144" fill="url(#emblem-tone)" stroke="var(--gold)" stroke-width="4"/>
    </svg>

    <div class="card__details">
      <h1 class="card__name">Sláine Dunleavy</h1>
      <p class="card__role">Massage Therapist</p>

      <ul class="contact">
        <li>
          <svg viewBox="0 0 24 24" aria-hidden="true"><path fill="currentColor" d="M6.6 10.8a15.1 15.1 0 0 0 6.6 6.6l2.2-2.2a1 1 0 0 1 1-.25 11.4 11.4 0 0 0 3.6.57 1 1 0 0 1 1 1V20a1 1 0 0 1-1 1A17 17 0 0 1 3 4a1 1 0 0 1 1-1h3.5a1 1 0 0 1 1 1c0 1.25.2 2.45.57 3.57a1 1 0 0 1-.25 1z"/></svg>
          (+353) 87 216 4093
        </li>
        <li>
          <svg viewBox="0 0 24 24" aria-hidden="true"><path fill="currentColor" d="M3 5h18v14H3z M4.5 6.5 12 12l7.5-5.5" stroke="var(--mint)" stroke-width="1.5"/></svg>
          slainemassage@example.ie
        </li>
      </ul>

      <ul class="services">
        <li>Swedish</li>
        <li>Deep Tissue</li>
        <li>Advanced Therapeutic</li>
      </ul>

      <p class="card__summary">QWTA qualified specialising in<br>advanced therapeutic and<br>deep tissue massage</p>
    </div>
  </div>
</body>
</html>
```